Web Design for guards MMJ transport and security services

Harbor Crest Protective solutions a tallow unified company, is looking for a designer to create a website that displays our service portfolio. We need marketing pictures and content to be created in a original and competitive fashion, intriguing to our customers. We will need forms on the website to be created for calendar booking (somehow integrate into exchange if possible) and general inquiry forms. There will need to be pages dedicated to our staff, MMJ trasnport & Courier services, our vehicles, alarm systems, video systems, video monitoring, private investigations, and surveillance aduit and compliance investigations, payment gateway integration, and general company information. I Have attached our main company logo. Also have a emphasis on being state licensed by the Colorado RPB. Have a link to our parent site, tallowcctv.example

Target Market(s)

Colorado Marijuana industry, MMJ transport services, guard services, armed gaurd services.

Contact Information for Business Card

Would like a sleek simple design highlighting what we offer. must match the website and have a overall professional straight to the point appearance.

Number of Pages Required

1 page

Colors
33b8a4
00a990
9bcb3c
acd036
cadf82
85cae6
33a6d7
0792cd

Requirements
Must have
• Easy to use, lots of images, professional.
Nice to have
• Creativity

```html
<!DOCTYPE html>
<html lang="en">
<head>
<meta charset="utf-8">
<title>Harbor Crest Protective Solutions</title>
<link rel="stylesheet" href="https://fonts.googleapis.com/css2?family=Oswald:wght@400;500&family=Open+Sans:ital,wght@0,400;0,600;0,700;1,400&display=swap">
<style>
:root{
  --green:#9bcb3c;
  --green-dark:#8fc030;
  --blue:#33a6d7;
  --teal:#33b8a4;
  --red:#d9262c;
  --ink:#444;
  --ink-soft:#555;
  --grey-bg:#f1f1f1;
  --footer-top:#3fb0e0;
  --footer-bottom:#2e9bd0;
}
*{box-sizing:border-box;margin:0;padding:0}
html,body{width:1200px;height:2403px;overflow:hidden}
body{position:relative;background:#fff;font-family:"Open Sans",Arial,sans-serif;color:var(--ink)}
.abs{position:absolute}

/* header */
.site-header{position:absolute;left:0;top:0;width:1200px;height:135px;background:#fff}
.utility-bar{position:absolute;left:408px;top:0;width:792px;height:52px;background:var(--green);clip-path:polygon(0 0,100% 0,100% 100%,22px 100%);display:flex;align-items:center;gap:0 36px;padding-left:32px}
.utility-bar a,.main-nav a{font-family:"Oswald",sans-serif;font-size:11px;color:#fff;text-decoration:none;text-transform:uppercase;white-space:nowrap}
.brand{position:absolute;left:160px;top:26px;display:flex;align-items:center;gap:10px}
.brand-dot{width:44px;height:44px;border-radius:50%;background:var(--red)}
.brand-name{font-family:"Oswald",sans-serif;font-weight:500;font-size:17px;line-height:1.05;color:var(--red);text-transform:uppercase}
.main-nav{position:absolute;left:394px;top:93px;display:flex;gap:26px}
.main-nav a{color:#333}
.main-nav a.active{color:var(--green)}

/* hero */
.hero{position:absolute;left:0;top:135px;width:1200px;height:477px;background:linear-gradient(180deg,#c8a56c 0%,#b99a6a 30%,#6d6f62 60%,#4f5550 100%)}
.hero-arrow{position:absolute;left:0;top:578px;width:34px;height:34px;background:#fff}
.hero-dots{position:absolute;left:580px;top:568px;display:flex;gap:6px}
.hero-dots span{width:12px;height:12px;border-radius:50%;background:#fff}
.hero-dots span.on{background:var(--green)}

/* section heads */
.section-title{position:absolute;left:0;width:1200px;text-align:center;font-family:"Oswald",sans-serif;font-weight:500;font-size:24px;color:var(--ink);text-transform:uppercase}
.stars{position:absolute;left:0;width:1200px;text-align:center;color:#777;font-size:15px;letter-spacing:1px}

.welcome-text{position:absolute;left:212px;top:716px;width:776px;text-align:center;font-size:10.5px;line-height:21px;color:var(--ink-soft)}
.welcome-text em{font-style:normal;color:var(--red)}

.feature{position:absolute;top:818px;width:285px;height:185px;color:#fff;text-align:center;padding:30px 30px 0}
.feature h3{font-family:"Oswald",sans-serif;font-weight:400;font-size:21px;text-transform:uppercase;margin-bottom:12px}
.feature p{font-size:10.5px;line-height:18px;opacity:.85}
.feature a{display:inline-block;margin-top:14px;font-size:11px;font-weight:700;color:#fff;text-decoration:none;text-transform:uppercase}
.feature.green{left:160px;background:var(--green)}
.feature.blue{left:457px;background:var(--blue)}
.feature.teal{left:753px;background:var(--teal)}

/* transport works */
.works{position:absolute;left:0;top:1045px;width:1200px;height:435px;background:var(--grey-bg);border-top:1px solid #e2e2e2}
.work{position:absolute;top:1141px;width:274px}
.work-photo{width:274px;height:158px}
.work h3{margin-top:24px;font-family:"Oswald",sans-serif;font-weight:400;font-size:20px;color:#333;text-transform:uppercase}
.work p{margin-top:8px;font-size:10.5px;line-height:18px;color:var(--ink-soft)}
.btn{display:inline-block;margin-top:20px;width:98px;height:33px;line-height:33px;text-align:center;background:var(--green);color:#fff;font-size:11.5px;font-weight:700;text-decoration:none;text-transform:uppercase}

/* services */
.services{position:absolute;left:0;top:1480px;width:1200px;height:333px;background:linear-gradient(180deg,#3a3d40,#2c2f31)}
.services .section-title,.services .stars{color:#fff}
.service{position:absolute;top:1605px;width:160px;margin-left:-80px;text-align:center;color:#fff}
.service svg{display:block;margin:0 auto}
.service span{display:block;margin-top:18px;font-size:15px;line-height:17px;font-weight:600}

/* testimonial */
.video{position:absolute;left:160px;top:1849px;width:425px;height:234px;background:linear-gradient(180deg,#9aa4ac,#6d7379)}
.play{position:absolute;left:182px;top:87px;width:60px;height:60px;border-radius:50%;background:#222;border:3px solid #fff}
.play::after{content:"";position:absolute;left:22px;top:16px;border-left:20px solid #fff;border-top:12px solid transparent;border-bottom:12px solid transparent}
.testimonial-title{position:absolute;left:620px;top:1845px;font-family:"Oswald",sans-serif;font-weight:500;font-size:24px;text-transform:uppercase;color:var(--ink)}
.quote{position:absolute;left:620px;top:1894px;width:420px;font-size:11.5px;font-style:italic;line-height:21px;color:var(--ink-soft)}
.quote b{font-family:"Oswald",sans-serif;font-style:italic;font-size:20px;color:#333;margin-right:6px}
.author{position:absolute;left:622px;top:2044px;font-size:14px;font-style:italic;color:#333}

/* footer */
.site-footer{position:absolute;left:0;top:2116px;width:1200px;height:236px;background:linear-gradient(180deg,var(--footer-top),var(--footer-bottom));color:#fff}
.seal{position:absolute;left:163px;top:59px;width:86px;height:86px;border-radius:50%;background:#e2b736;border:5px solid #2a2a2a}
.partner{position:absolute;left:262px;top:80px;display:flex;align-items:center;gap:8px;font-family:"Open Sans",sans-serif;font-weight:600;font-size:21px;text-transform:uppercase}
.partner i{width:34px;height:34px;border-radius:50%;border:3px solid #fff}
.footer-col h4{font-size:16px;font-weight:400;text-transform:uppercase;margin-bottom:12px}
.contact{position:absolute;left:501px;top:36px}
.contact li{list-style:none;font-size:10.5px;line-height:20px;padding-left:18px;position:relative}
.contact li::before{content:"";position:absolute;left:2px;top:7px;width:6px;height:6px;background:#fff;border-radius:50%}
.newsletter{position:absolute;left:732px;top:36px}
.newsletter p{font-size:11px;margin-top:-6px}
.signup{margin-top:14px;display:flex}
.signup span{width:228px;height:36px;background:#fff;color:#888;font-size:10.5px;font-style:italic;line-height:36px;padding-left:12px}
.signup strong{width:77px;height:36px;background:var(--green);text-align:center;line-height:36px;font-size:11.5px;text-transform:uppercase}
.social{margin-top:14px;display:flex;gap:7px}
.social i{width:27px;height:27px;border-radius:50%;border:1.5px solid #fff}
.legal{position:absolute;left:0;top:2352px;width:1200px;height:51px;background:var(--green);color:#fff;font-size:10.5px;line-height:51px;text-align:center}
</style>
</head>
<body>

<header class="site-header">
  <nav class="utility-bar">
    <a href="#">Video Monitoring</a><a href="#">Private Investigations</a><a href="#">Surveillance Audit</a><a href="#">Compliance Investigations</a><a href="#">Contact Us</a>
  </nav>
  <div class="brand"><span class="brand-dot"></span><span class="brand-name">Harbor Crest<br>Protective</span></div>
  <nav class="main-nav">
    <a class="active" href="#">Home</a><a href="#">About Us</a><a href="#">Our Staff</a><a href="#">MMJ Trasnport &amp; Courier Services</a><a href="#">Our Vehicles</a><a href="#">Alarm Systems</a><a href="#">Video Systems</a>
  </nav>
</header>

<div class="hero" role="img" aria-label="Highway at sunset with cars and a delivery truck passing fields"></div>
<svg class="abs" style="left:0;top:578px" width="34" height="34"><rect width="34" height="34" fill="#fff"/><path d="M10 8l10 9-10 9" fill="none" stroke="#d9262c" stroke-width="4"/></svg>
<div class="hero-dots"><span></span><span class="on"></span><span></span></div>

<h2 class="section-title" style="top:646px">Welcome to Harbor Crest Protective Solutions</h2>
<div class="stars" style="top:680px">★★★</div>
<p class="welcome-text">Sed ut perspiciatis unde omnis iste nloreatus error sit volupt atem <em>accusantiuloremm</em> dol ore mq ue laudantiumtota m rem aperiam, eaque ipsa quae ab illo inventore ver itatis et asi <em>architecto beatae vita sit aspernatued</em> ut perspiciatis unde omnis iste nloreatus error sit volupt atem accusantium doloremque laudantiumtota m rem aperiam, eaque ipsa qu ae ab illo inventore ver itatis et quasi architecto beatae <em>vitaesit aspernad</em> ut perspiciatis unde omnis iste nlorea tus error sit volupt atem accusantium dolore mque laudantiumtota m rem aperiam, eaque ipsa quae ab illo invento.ver itatis et asi</p>

<div class="feature green"><h3>About Tallow</h3><p>Sed ut perspiciatis unde omnis iste natuserr or sit voluptatem accusantium doloremque lau dantium, totam rem aperiam, eaque.</p><a href="#">Read More</a></div>
<div class="feature blue"><h3>Trasnport &amp; Courier</h3><p>Sed ut perspiciatis unde omnis iste natuserr or sit voluptatem accusantium doloremque lau dantium, totam rem aperiam, eaque.</p><a href="#">Read More</a></div>
<div class="feature teal"><h3>Security Services</h3><p>Sed ut perspiciatis unde omnis iste natuserr or sit voluptatem accusantium doloremque lau dantium, totam rem aperiam, eaque.</p><a href="#">Read More</a></div>

<section class="works"></section>
<h2 class="section-title" style="top:1068px">Transport Works</h2>
<div class="stars" style="top:1102px">★★★</div>
<article class="work" style="left:160px"><div class="work-photo" role="img" aria-label="Courier holding a clipboard beside stacked parcels" style="background:linear-gradient(135deg,#d8c6a8,#9b8a70)"></div><h3>Courier Services</h3><p>Sed ut perspiciatis unde omnis iste nloreatus error sit volupt atem accusantiuloremm dol ore mq ue lauda ntiumtota m rem aperiam, eaque ipsa qua</p><a class="btn" href="#">Read More</a></article>
<article class="work" style="left:462px"><div class="work-photo" role="img" aria-label="Red alarm bell on a glass office wall" style="background:linear-gradient(135deg,#6f8c86,#3f5552)"></div><h3>Alarm Systems</h3><p>Sed ut perspiciatis unde omnis iste nloreatus error sit volupt atem accusantiuloremm dol ore mq ue lauda ntiumtota m rem aperiam, eaque ipsa qua</p><a class="btn" href="#">Read More</a></article>
<article class="work" style="left:764px"><div class="work-photo" role="img" aria-label="Dome security camera over a city at night" style="background:linear-gradient(135deg,#2f3f66,#1c2236)"></div><h3>Surveillance Audit</h3><p>Sed ut perspiciatis unde omnis iste nloreatus error sit volupt atem accusantiuloremm dol ore mq ue lauda ntiumtota m rem aperiam, eaque ipsa qua</p><a class="btn" href="#">Read More</a></article>

<section class="services" role="img" aria-label="Dark blurred motorway traffic background"></section>
<h2 class="section-title" style="top:1518px;color:#fff">Services &amp; Solutions</h2>
<div class="stars" style="top:1552px;color:#fff">★★★</div>

<div class="service" style="left:213px"><svg width="70" height="82" viewBox="0 0 70 82"><path d="M35 3 L66 14 V44 C66 62 50 74 35 79 C20 74 4 62 4 44 V14 Z" fill="none" stroke="#fff" stroke-width="4"/><path d="M35 24 l3 12 12 6v4l-12-3-1 9 4 3v3l-6-2-6 2v-3l4-3-1-9-12 3v-4l12-6z" fill="#fff"/></svg><span>Air<br>Import/Export</span></div>
<div class="service" style="left:367px"><svg width="70" height="82" viewBox="0 0 70 82"><path d="M35 3 L66 14 V44 C66 62 50 74 35 79 C20 74 4 62 4 44 V14 Z" fill="none" stroke="#fff" stroke-width="4"/><g fill="none" stroke="#fff" stroke-width="3.5"><circle cx="35" cy="25" r="4"/><path d="M35 29v30M27 36h16M22 47c2 9 8 12 13 12s11-3 13-12"/></g></svg><span>Ocean<br>Import/Export</span></div>
<div class="service" style="left:521px"><svg width="70" height="82" viewBox="0 0 70 82"><path d="M35 3 L66 14 V44 C66 62 50 74 35 79 C20 74 4 62 4 44 V14 Z" fill="none" stroke="#fff" stroke-width="4"/><circle cx="35" cy="31" r="8" fill="#fff"/><path d="M21 57c0-9 6-14 14-14s14 5 14 14z" fill="#fff"/></svg><span>Customs<br>Brokerage</span></div>
<div class="service" style="left:674px"><svg width="70" height="82" viewBox="0 0 70 82"><path d="M35 3 L66 14 V44 C66 62 50 74 35 79 C20 74 4 62 4 44 V14 Z" fill="none" stroke="#fff" stroke-width="4"/><path d="M28 22h14l8 36H20z" fill="#fff"/><path d="M35 25v6M35 36v7M35 48v7" stroke="#333" stroke-width="3"/></svg><span>Domestic<br>Transportation</span></div>
<div class="service" style="left:830px"><svg width="70" height="82" viewBox="0 0 70 82"><path d="M35 3 L66 14 V44 C66 62 50 74 35 79 C20 74 4 62 4 44 V14 Z" fill="none" stroke="#fff" stroke-width="4"/><path d="M35 22 L54 39h-5v16H40V45h-10v10h-9V39h-5z" fill="#fff"/></svg><span>Warehousing<br>Services</span></div>
<div class="service" style="left:984px"><svg width="70" height="82" viewBox="0 0 70 82"><path d="M35 3 L66 14 V44 C66 62 50 74 35 79 C20 74 4 62 4 44 V14 Z" fill="none" stroke="#fff" stroke-width="4"/><path d="M17 28h24v20H17zM43 34h8l6 7v7H43z" fill="#fff"/><circle cx="24" cy="51" r="4" fill="#fff"/><circle cx="49" cy="51" r="4" fill="#fff"/></svg><span>Project<br>Cargo Services</span></div>

<div class="video" role="img" aria-label="Video still of two trucks on a motorway"><span class="play"></span></div>
<h2 class="testimonial-title">Testimonials</h2>
<p class="quote"><b>“</b>Sed ut perspiciatis unde omnis iste natus error sit voluptatem accu san tium dol oremque laudantium, totam rem aperiam, eaque ipsa quae ab illo inv entore ver itatis et quasi architecto beatae vitae dicta sunt explicaboemo enim ips am voluptatem quia voluptas sit aspernatur d ut perspiciatis unde omnis iste nat us error sit voluptatem accusantium dol oremque laudantium, totam rem ape riam, eaque ipsa quae ab illo inv entore ver itatis et quasi. <b>”</b></p>
<p class="author">Dana Merrow, City Name</p>

<footer class="site-footer">
  <span class="seal" aria-label="State license badge"></span>
  <div class="partner"><i></i>Tallow</div>
  <div class="footer-col contact">
    <h4>Contact Us</h4>
    <ul>
      <li>Postal address: PO Box 214,<br>Marlow Ridge Lane</li>
      <li>Phone: 555-014-2297</li>
      <li>Fax: 555-014-2298</li>
      <li>info@harborcrest.example</li>
    </ul>
  </div>
  <div class="footer-col newsletter">
    <h4>Sign Up Newsletter</h4>
    <p>Please sign up here for latest deals</p>
    <div class="signup"><span>Email address</span><strong>Sign Up</strong></div>
    <div class="social"><i></i><i></i><i></i><i></i><i></i></div>
  </div>
</footer>
<div class="legal">© 2016 Harbor Crest Protective solutions,. All right reserved &nbsp;Term of Use. Privacy Policy</div>

</body>
</html>
```